HOT TUB - SPAS service needs an business card

I need an business for my company who his specialise in a maintenance,water treatment and cleaning of Hot Tub - Spas for commercial and residential customers. The company operate mainly in the ski resort of Chamonix, Megève and St Gervais. The final product should communicate pure water, cleanest and professional for luxury property's.
I have upload a logo but any improvement on it is welcome.(color,size, details etc..) or any other idea. Thank you
Company Name: 58 BAINS
My name: Lucien Marchetti
Email: lucimarch@examplemail.net
Tel: +33 (0)6 71 58 29 64
Description to be on the card in french(first langage) and in English:
- Spas service
- Entretien, traitement eau, nettoyage.
- Maintenance, water treatment, cleaning.
Industry/Entity Type
Residential
Colors
Designer to choose colors to be used in the design.
Look and feel
Each slider illustrates characteristics of the customer's brand and the style your logo design should communicate.

```html
<!DOCTYPE html>
<html lang="fr">
<head>
<meta charset="utf-8">
<title>58 BAINS – Cartes de visite</title>
<link rel="stylesheet" href="https://fonts.googleapis.com/css2?family=Source+Sans+3:wght@400;600;700&display=swap">
<style>
  :root {
    --backdrop: #e9edf1;
    --front-blue: #1ea5f7;
    --back-blue: #0b79d9;
    --deep-blue: #0b5ccc;
    --pale-blue: #9dd6fa;
    --white: #ffffff;
    --drawing-tint: rgba(255, 255, 255, 0.16);
  }
  * { box-sizing: border-box; margin: 0; padding: 0; }
  html, body {
    width: 1200px;
    height: 1183px;
    overflow: hidden;
    background: var(--backdrop);
    font-family: "Source Sans 3", "Myriad Pro", sans-serif;
    color: var(--white);
  }
  .canvas { position: relative; width: 1200px; height: 1183px; }

  .card {
    position: absolute;
    width: 911px;
    height: 520px;
    overflow: hidden;
    box-shadow: 0 6px 18px rgba(20, 40, 70, 0.18);
  }
  .card--front { left: 31px; top: 36px; background: var(--front-blue); }
  .card--back  { left: 220px; top: 618px; background: var(--back-blue); }

  .chalet-drawing {
    position: absolute;
    border-radius: 6px;
    background: linear-gradient(180deg, var(--drawing-tint), rgba(255,255,255,0.06));
  }
  .card--front .chalet-drawing { left: 183px; top: 60px; width: 580px; height: 158px; }
  .card--back  .chalet-drawing { left: 116px; top: 100px; width: 700px; height: 194px; }

  .holder-name {
    position: absolute;
    left: 104px;
    top: 312px;
    font-size: 31px;
    font-weight: 700;
    line-height: 38px;
  }
  .contact-divider {
    position: absolute;
    left: 417px;
    top: 287px;
    width: 1px;
    height: 81px;
    background: rgba(255, 255, 255, 0.7);
  }
  .contact-list { position: absolute; left: 442px; top: 286px; list-style: none; }
  .contact-item {
    display: flex;
    align-items: center;
    gap: 12px;
    height: 48px;
    font-size: 28px;
    font-weight: 600;
  }
  .contact-item svg { width: 26px; height: 26px; flex: none; }

  .wave { position: absolute; left: 0; top: 0; width: 911px; height: 520px; }
  .company-name {
    position: absolute;
    left: 145px;
    top: 446px;
    font-size: 40px;
    font-weight: 600;
    line-height: 48px;
    letter-spacing: 0.5px;
  }

  .services {
    position: absolute;
    left: 0;
    top: 358px;
    width: 100%;
    text-align: center;
  }
  .services-title { font-size: 31px; font-weight: 700; line-height: 44px; }
  .services-line { font-size: 30px; font-weight: 400; line-height: 42px; }
  .services-line span + span { margin-left: 14px; }
</style>
</head>
<body>
<main class="canvas">

  <section class="card card--front" aria-label="Recto de la carte">
    <div class="chalet-drawing" role="img" aria-label="Line drawing of mountains, a chalet and a hot tub"></div>

    <p class="holder-name">Lucien Marchetti</p>
    <div class="contact-divider"></div>
    <ul class="contact-list">
      <li class="contact-item">
        <svg viewBox="0 0 24 24" aria-hidden="true"><circle cx="12" cy="12" r="10.5" fill="none" stroke="#fff" stroke-width="2"/><path d="M9 6.5c-1.5 1-2 3-.8 5.6 1.3 2.8 3.4 4.6 5.5 5 1 .2 1.8-.3 2.3-1l-2-2-1.4.8c-1-.5-2.2-2-2.6-3.2l1.1-1.1-1.3-2.7z" fill="#fff"/></svg>
        <span>+33 (0)6 71 58 29 64</span>
      </li>
      <li class="contact-item">
        <svg viewBox="0 0 24 24" aria-hidden="true"><path d="M2 10l10-7 10 7v11H2z" fill="#fff"/><path d="M2 10l10 7 10-7" fill="none" stroke="#1ea5f7" stroke-width="1.6"/><rect x="7" y="7" width="10" height="5" fill="#1ea5f7"/><path d="M8.5 8.6h7M8.5 10.4h5" stroke="#fff" stroke-width="1"/></svg>
        <span>lucimarch@examplemail.net</span>
      </li>
    </ul>

    <svg class="wave" viewBox="0 0 911 520" aria-hidden="true">
      <path d="M0 438 C120 405 260 405 420 450 C560 490 720 500 911 403 L911 520 L0 520 Z" fill="var(--pale-blue)"/>
      <path d="M0 452 C130 420 270 420 430 466 C570 503 740 505 911 430 L911 520 L0 520 Z" fill="var(--deep-blue)"/>
      <path d="M420 478 C560 525 740 520 911 452" fill="none" stroke="var(--pale-blue)" stroke-width="8"/>
    </svg>
    <p class="company-name">58 BAINS</p>
  </section>

  <section class="card card--back" aria-label="Verso de la carte">
    <div class="chalet-drawing" role="img" aria-label="Line drawing of mountains, a chalet and a hot tub"></div>
    <div class="services">
      <h2 class="services-title">SPAS SERVICES</h2>
      <p class="services-line"><span>•Entretien</span><span>•traitement eau</span><span>•nettoyage</span></p>
      <p class="services-line"><span>•Maintenance</span><span>•water treatment</span><span>•cleaning.</span></p>
    </div>
  </section>

</main>
</body>
</html>
```